Printer Cartridges Supplier Namecard

Attached is my company logo and the design of my current namecard. I would like to have a more special look for it. Can have a little cuteness too rather than those normal standard feel. I'm a supplier mainly dealing with original and compatible printer toner cartridges, some other products like paper supplies as well.

Target Market(s)

Companies, businesses, corporates

Industry/Entity Type

It Company

Contact Information for Business Card

Logo, name, contact, address, supplies and maybe a slogan

Colors
85cae6
33a6d7
3176b5
0255a3
0792cd
85abd2

Requirements
Must have
• Logo, name, contact and address basic details.
• Must include some pictures, not just rearrange what I'm currently having.
Nice to have
• Be creative and bold, a diiferent traditional feel.

```html
<!DOCTYPE html>
<html lang="en">
<head>
<meta charset="utf-8">
<title>printnest namecard</title>
<link href="https://fonts.googleapis.com/css2?family=Work+Sans:wght@400;500&family=Quicksand:wght@500&display=swap" rel="stylesheet">
<style>
  :root {
    --backdrop: #1b1b1b;
    --card-white: #ffffff;
    --brand-blue: #62b4e3;
    --ink-grey: #505050;
    --band-grey: #5a5a5a;
    --text-dark: #3a3a3a;
  }
  * { margin: 0; padding: 0; box-sizing: border-box; }
  html, body { width: 1200px; height: 897px; overflow: hidden; }
  body { background: var(--backdrop); position: relative; font-family: "Work Sans", sans-serif; }

  .card {
    position: absolute; left: 303px; width: 595px; height: 339px;
    border-radius: 22px; overflow: hidden;
    box-shadow: 0 8px 18px rgba(0,0,0,0.6);
  }
  .card-front { top: 92px; background: var(--card-white); }
  .card-back { top: 469px; background: var(--brand-blue); }

  .front-bands { position: absolute; left: 0; bottom: 0; }

  .brand { position: absolute; display: flex; align-items: center; }
  .brand-mark { display: block; flex: none; background: var(--brand-blue); border-radius: 6px; }
  .brand-text { display: flex; flex-direction: column; white-space: nowrap; }
  .brand-name { font-family: "Quicksand", sans-serif; font-weight: 500; line-height: 1; }
  .brand-tagline { font-family: "Quicksand", sans-serif; font-weight: 500; }

  .card-front .brand { left: 38px; top: 138px; gap: 10px; }
  .card-front .brand-mark { width: 64px; height: 64px; }
  .card-front .brand-name { font-size: 40px; color: var(--ink-grey); }
  .card-front .brand-tagline { font-size: 7px; color: var(--ink-grey); margin-top: 3px; }

  .divider { position: absolute; left: 306px; top: 90px; width: 2px; height: 160px; background: var(--brand-blue); }

  .contact { position: absolute; left: 339px; top: 90px; color: var(--text-dark); }
  .person-name { font-size: 19px; font-weight: 500; color: var(--brand-blue); line-height: 1.05; }
  .person-role { font-size: 14px; letter-spacing: 0.5px; line-height: 1.3; }
  .person-hp { font-size: 14px; letter-spacing: 0.5px; line-height: 1.2; }
  .person-hp .label { color: var(--brand-blue); }
  .address { font-size: 13.5px; line-height: 1.3; margin-top: 12px; padding-left: 3px; }
  .channels { list-style: none; margin-top: 10px; font-size: 13.5px; line-height: 1.3; }
  .channels li { display: flex; align-items: center; gap: 10px; }
  .channels svg { width: 8px; height: 8px; flex: none; }

  .card-back .brand { left: 0; right: 0; top: 125px; gap: 14px; justify-content: center; }
  .card-back .brand-mark { width: 88px; height: 88px; background: var(--card-white); border-radius: 8px; }
  .card-back .brand-name { font-size: 48px; color: var(--card-white); }
  .card-back .brand-tagline { font-size: 10px; color: var(--card-white); margin-top: 4px; }
  .card-back .web { position: absolute; left: 0; right: 0; top: 298px; text-align: center; color: var(--card-white); font-size: 13px; }
</style>
</head>
<body>
  <section class="card card-front">
    <svg class="front-bands" width="595" height="35" viewBox="0 0 595 35">
      <rect x="0" y="14" width="312" height="21" fill="var(--band-grey)"/>
      <polygon points="305,35 334,0 595,0 595,35" fill="var(--card-white)"/>
      <polygon points="312,35 341,0 595,0 595,35" fill="var(--brand-blue)"/>
    </svg>

    <div class="brand">
      <span class="brand-mark"></span>
      <div class="brand-text">
        <span class="brand-name">printnest</span>
        <span class="brand-tagline">Compatible printer ink and toner solutions</span>
      </div>
    </div>

    <div class="divider"></div>

    <div class="contact">
      <p class="person-name">MIRA TAN</p>
      <p class="person-role">Sales Executive</p>
      <p class="person-hp"><span class="label">HP</span> 9184 0736</p>
      <p class="address">41A Lorong Mei Crescent<br>05-112 Singapore 530041</p>
      <ul class="channels">
        <li><svg viewBox="0 0 10 10"><path d="M2 1 L4 1 L4.5 3 L3.5 4 Q4.5 6 6 6.5 L7 5.5 L9 6 L9 8 Q5 9 2 5 Q1 3 2 1Z" fill="var(--brand-blue)"/></svg>612-408-3357</li>
        <li><svg viewBox="0 0 10 10"><rect x="1" y="2" width="8" height="6" fill="none" stroke="var(--brand-blue)" stroke-width="1"/><path d="M1 2 L5 5.5 L9 2" fill="none" stroke="var(--brand-blue)" stroke-width="1"/></svg>mira@printnest.sg</li>
        <li><svg viewBox="0 0 10 10"><circle cx="5" cy="5" r="4" fill="none" stroke="var(--brand-blue)" stroke-width="1"/><path d="M1 5 H9 M5 1 V9" stroke="var(--brand-blue)" stroke-width="0.8"/></svg>www.printnest.sg</li>
      </ul>
    </div>
  </section>

  <section class="card card-back">
    <div class="brand">
      <span class="brand-mark"></span>
      <div class="brand-text">
        <span class="brand-name">printnest</span>
        <span class="brand-tagline">Compatible printer ink and toner solutions</span>
      </div>
    </div>
    <p class="web">www.printnest.sg</p>
  </section>
</body>
</html>
```